Print materials for 3-star hotel

We are changing up our print materials (notepads, letterheads, key card jackets, small flyer for the room rates) We are a 3 star business hotel in the Philippines and have mainly used grey tones and clean, simple lines. See attached photos for logo and hotel interior photos.

Target Market(s)

Business

Contact Information for Business Card

Corvale Terrace Hotel
Lindwell Banca Avenue corner Tolenta St Cebu City 6000 Philippines
Tel: +63 32 481 7302
Mobile: +63 917 648 2095
www.corvaleterracehotel.example

Font styles to use
Serif
Sans Serif

Requirements
Must have
• Simple
• Readable font and font size
Nice to have
• Neutral colors, grey and taupes
Should not have
• No purples and bright blues

```html
<!DOCTYPE html>
<html lang="en">
<head>
<meta charset="utf-8">
<title>Corvale Terrace Hotel — Business Card</title>
<link rel="stylesheet" href="https://fonts.googleapis.com/css2?family=Cinzel:wght@400;600&family=Jost:wght@400&display=swap">
<style>
  :root {
    --backdrop: #2b2b2c;
    --card: #161617;
    --card-edge: #0c0c0d;
    --ink: #f1f1f1;
    --ink-soft: #d9d9d9;
  }
  * { box-sizing: border-box; margin: 0; padding: 0; }
  html, body {
    width: 1200px;
    height: 1017px;
    overflow: hidden;
    background: var(--backdrop);
  }
  .canvas {
    position: relative;
    width: 1200px;
    height: 1017px;
  }
  .card {
    position: absolute;
    width: 560px;
    height: 320px;
    background: var(--card);
    border: 1px solid var(--card-edge);
    box-shadow: 0 18px 40px rgba(0, 0, 0, 0.45);
    overflow: hidden;
  }
  .card--front { left: 70px; top: 170px; }
  .card--back  { left: 570px; top: 540px; }

  /* Front: brand lockup */
  .brand {
    position: absolute;
    left: 0; right: 0; top: 92px;
    display: flex;
    flex-direction: column;
    align-items: center;
    color: var(--ink);
    font-family: "Cinzel", serif;
  }
  .brand__mark {
    width: 40px;
    height: 40px;
    background: var(--ink);
    margin-bottom: 22px;
  }
  .brand__name {
    font-size: 24px;
    font-weight: 400;
    letter-spacing: 0.22em;
    line-height: 1;
  }
  .brand__sub {
    margin-top: 8px;
    font-size: 24px;
    font-weight: 400;
    letter-spacing: 0.22em;
    line-height: 1;
  }

  /* Back: contact block */
  .contact {
    position: absolute;
    left: 190px;
    top: 92px;
    color: var(--ink);
    white-space: nowrap;
  }
  .contact__name {
    font-family: "Cinzel", serif;
    font-weight: 600;
    font-size: 21px;
    letter-spacing: 0.03em;
    line-height: 1.05;
  }
  .contact__role {
    font-family: "Cinzel", serif;
    font-size: 12px;
    letter-spacing: 0.06em;
    padding-left: 22px;
    margin-bottom: 10px;
  }
  .contact__line {
    font-family: "Jost", sans-serif;
    font-size: 14px;
    line-height: 1.3;
    color: var(--ink-soft);
  }
  .contact__line--gap { margin-top: 4px; }
</style>
</head>
<body>
<main class="canvas">
  <section class="card card--front" aria-label="Business card front">
    <div class="brand">
      <span class="brand__mark"></span>
      <span class="brand__name">Corvale Terrace</span>
      <span class="brand__sub">Hotel</span>
    </div>
  </section>

  <section class="card card--back" aria-label="Business card back">
    <div class="contact">
      <p class="contact__name">Elias Marren</p>
      <p class="contact__role">President</p>
      <p class="contact__line">Lindwell Banca Avenue corner Tolenta St</p>
      <p class="contact__line">Cebu City 6000 Philippines</p>
      <p class="contact__line contact__line--gap">+63 32 481 7302</p>
      <p class="contact__line">elias@corvaleterrace.example</p>
      <p class="contact__line">www.corvaleterracehotel.example</p>
    </div>
  </section>
</main>
</body>
</html>
```